Vantor Wear and Fuel is looking for a Clothing/Supplement Online Store Website!

Must be convenient, and user friendly, with vibrant colors that catch the eye!

Target Market(s)

Athletes, and Fashion Customers

Industry/Entity Type

Fitness

Coding

Coded - Design and coding required

Number of Pages Required

3 page

Font styles to use
Decorative

Colors

Designer to choose colors to be used in the design.

Requirements
Must have
• Somewhere to feature products, features to promote discounts and make announcements.
Nice to have
• My logos on each page

```html
<!DOCTYPE html>
<html lang="en">
<head>
<meta charset="utf-8">
<title>Vantor Wear and Fuel — Home</title>
<link rel="stylesheet" href="https://fonts.googleapis.com/css2?family=Mulish:wght@400;600;700&family=Crimson+Text:wght@400;600&family=Oswald:wght@400;500&display=swap">
<style>
:root{
  --orange:#e8792a;
  --gold:#f0a22a;
  --steel:#557a8e;
  --ink:#222;
  --text:#444;
  --muted:#777;
  --hero-sky:#d9eaf3;
  --band-grey:#e3e3e3;
  --soft:#f7f7f9;
  --footer:#2b2b2d;
  --line:#e6e6e6;
  --star:#f5b400;
}
*{box-sizing:border-box;margin:0;padding:0}
html,body{width:1200px;height:3924px;overflow:hidden}
body{font-family:'Mulish',sans-serif;color:var(--text);background:#fff;position:relative}
.abs{position:absolute}
a{color:inherit;text-decoration:none}

/* header */
.site-header{position:absolute;left:0;top:0;width:1200px;height:78px;background:#fff}
.brand{position:absolute;left:142px;top:26px;display:flex;align-items:center;gap:8px;font-weight:700;font-size:17px;color:var(--ink);letter-spacing:1px}
.brand-mark{width:12px;height:12px;background:var(--ink)}
.main-nav{position:absolute;left:471px;top:37px;display:flex;gap:36px;font-size:12.5px;color:#333;letter-spacing:.3px}
.main-nav .active{color:var(--orange)}
.search{position:absolute;left:932px;top:30px;width:127px;height:27px;border:1.5px solid #333;border-radius:14px;font-size:10px;color:#666;padding:6px 0 0 14px}
.search svg{position:absolute;right:9px;top:6px}

/* hero */
.hero{position:absolute;left:0;top:78px;width:1200px;height:493px;background:var(--hero-sky);overflow:hidden}
.hero-photo{position:absolute;left:600px;top:0;width:380px;height:493px;background:linear-gradient(180deg,#c7a48f,#5b5a4a 55%,#3a3a33)}
.hero-stroke{position:absolute;left:1040px;top:40px;width:200px;height:360px;background:linear-gradient(160deg,rgba(255,255,255,.7),rgba(255,255,255,.2))}
.diamond{position:absolute;left:207px;top:95px;width:302px;height:302px;background:#fff;transform:rotate(45deg)}
.diamond-line{position:absolute;left:216px;top:103px;width:302px;height:302px;border:1.5px solid #fff;transform:rotate(45deg)}
.hero-copy{position:absolute;left:206px;top:156px;width:304px;text-align:center}
.hero-copy .kicker{font-family:'Oswald',sans-serif;font-size:22px;color:#222;letter-spacing:.5px}
.hero-copy .deal{font-family:'Oswald',sans-serif;font-weight:500;font-size:38px;color:#222;margin-top:2px}
.hero-copy p{font-size:12.5px;line-height:24px;color:#444;margin-top:12px}
.btn-outline{display:inline-block;border:1.5px solid var(--gold);color:var(--gold);border-radius:16px;font-size:12px;font-weight:600;padding:5px 12px}
.hero-copy .btn-outline{margin-top:10px}
.hero-arrow{position:absolute;top:224px;width:44px;height:44px;border-radius:50%;background:rgba(255,255,255,.35)}

/* section titles */
.section-title{position:absolute;left:0;width:1200px;text-align:center;font-family:'Crimson Text',serif;font-size:36px;color:var(--orange);letter-spacing:2px;text-transform:uppercase}

/* products */
.product-card{position:absolute;width:291px;height:425px;border:1px solid var(--line);background:#fff}
.product-img{height:268px;background:#f7f7f7;display:flex;align-items:center;justify-content:center}
.product-img span{display:block;width:110px;height:200px;border-radius:10px}
.badge{position:absolute;right:22px;top:14px;width:36px;height:36px;border-radius:50%;background:var(--steel)}
.rating{margin:24px 0 0 12px;font-size:11px;color:#333}
.rating b{color:var(--star);font-weight:400;letter-spacing:1px}
.product-name{margin:8px 0 0 12px;font-size:18px;font-weight:600;color:#222}
.product-card .btn-outline{margin:16px 0 0 15px;padding:5px 28px;font-size:12px}
.btn-solid{position:absolute;background:var(--steel);color:#fff;border-radius:18px;text-align:center;font-size:15px;font-weight:600}

/* promo band */
.promo{position:absolute;left:0;top:1770px;width:1200px;height:388px;background:var(--band-grey)}
.promo-photo{position:absolute;left:107px;top:0;width:390px;height:388px;background:linear-gradient(180deg,#b8a99a,#c9d3e6 45%,#d8d8d8)}
.promo h2{position:absolute;left:586px;top:104px;font-family:'Crimson Text',serif;font-weight:600;font-size:36px;color:#1f1f1f;letter-spacing:1.5px}
.promo .sub{position:absolute;left:586px;top:150px;font-size:17px;color:var(--orange);letter-spacing:.3px}
.promo p{position:absolute;left:586px;top:184px;width:470px;font-size:12.5px;line-height:23px;color:#444}

/* about */
.about-copy{position:absolute;left:142px;top:2306px;width:500px;font-size:14px;line-height:25.5px;color:#333}
.about-copy p{margin-bottom:11px}
.about-frame{position:absolute;left:664px;top:2327px;width:355px;height:297px;border:4px solid #f5dcae}
.about-photo{position:absolute;left:685px;top:2306px;width:374px;height:296px;background:linear-gradient(135deg,#a9c6d6,#d8b987 50%,#6f8ea8)}

/* blogs */
.blogs{position:absolute;left:0;top:2699px;width:1200px;height:636px;background:var(--soft)}
.blog-card{position:absolute;top:140px;width:291px;height:350px;background:#fff}
.blog-img{height:169px}
.blog-card h3{margin:22px 12px 0;font-size:13.5px;line-height:23px;font-weight:700;color:#222}
.blog-card p{margin:10px 12px 0;font-size:12px;line-height:23px;color:#444}
.round-arrow{position:absolute;top:307px;width:34px;height:34px;border-radius:50%;border:1px solid #ccc;background:#fff}
.round-arrow svg{position:absolute;left:10px;top:10px}

/* newsletter */
.newsletter{position:absolute;left:0;top:3335px;width:1200px;height:249px;background:linear-gradient(135deg,#f09a1f,#f2ab34 60%,#ee9b25)}
.newsletter h2{position:absolute;left:0;top:50px;width:1200px;text-align:center;font-family:'Crimson Text',serif;font-size:36px;color:#fff;letter-spacing:2.5px}
.newsletter .lede{position:absolute;left:0;top:103px;width:1200px;text-align:center;font-size:16px;color:#fff}
.email-field{position:absolute;left:372px;top:144px;width:455px;height:35px;border-radius:18px;background:#fff;font-size:12px;color:#999;padding:10px 0 0 20px}
.email-field .btn-solid{right:0;top:0;width:124px;height:35px;line-height:35px;font-size:14px;letter-spacing:.3px}

/* footer */
.site-footer{position:absolute;left:0;top:3584px;width:1200px;height:340px;background:var(--footer);color:#ddd}
.foot-head{position:absolute;top:72px;font-family:'Crimson Text',serif;font-size:16px;letter-spacing:1.5px;color:#eee}
.quick-links{position:absolute;left:142px;top:108px;list-style:none;font-size:13px;line-height:30.5px}
.quick-links li::before{content:"›";margin-right:10px;color:#aaa}
.contact-row{position:absolute;left:330px;display:flex;gap:16px;font-size:13px;line-height:20px}
.icon-ring{width:28px;height:28px;border-radius:50%;border:1.5px solid var(--gold);flex:none;display:flex;align-items:center;justify-content:center}
.social-row{position:absolute;left:651px;display:flex;align-items:center;gap:12px;font-size:13px}
.social-row i{width:24px;height:24px;border-radius:50%;border:1.5px solid #ddd;display:block}
.foot-brand{position:absolute;left:855px;top:174px;display:flex;align-items:center;gap:12px;font-size:30px;font-weight:700;color:#bbb;letter-spacing:1px}
.foot-brand i{width:24px;height:24px;background:#bbb;display:block}
.foot-rule{position:absolute;left:142px;top:298px;width:917px;height:1px;background:#444}
.copyright{position:absolute;left:0;top:308px;width:1200px;text-align:center;font-size:12px;color:#ccc}
</style>
</head>
<body>

<header class="site-header">
  <a class="brand" href="#"><span class="brand-mark"></span>VANTOR</a>
  <nav class="main-nav">
    <a class="active" href="#">HOME</a><a href="#">ABOUT US</a><a href="#">PRODUCTS</a><a href="#">BLOG</a><a href="#">CONTACT US</a>
  </nav>
  <div class="search">Search
    <svg width="13" height="13" viewBox="0 0 13 13"><circle cx="5.5" cy="5.5" r="4" fill="none" stroke="#333" stroke-width="1.6"/><line x1="8.5" y1="8.5" x2="12" y2="12" stroke="#333" stroke-width="1.6"/></svg>
  </div>
</header>

<section class="hero">
  <div class="hero-stroke" role="img" aria-label="Loose white brush stroke decoration"></div>
  <div class="hero-photo" role="img" aria-label="Model in a dark floral wrap dress seated on a stool"></div>
  <div class="diamond-line"></div>
  <div class="diamond"></div>
  <div class="hero-copy">
    <div class="kicker">HOT PRODUCTS</div>
    <div class="deal">50% OFF 2019</div>
    <p>Nullam tincidunt lobortis felis, in accumsan<br>lacus vari in donec ut diam eget augu.</p>
    <a class="btn-outline" href="#">Discover More</a>
  </div>
  <div class="hero-arrow" style="left:36px"><svg width="44" height="44"><polyline points="25,14 17,22 25,30" fill="none" stroke="#fff" stroke-width="1.5"/></svg></div>
  <div class="hero-arrow" style="left:1118px"><svg width="44" height="44"><polyline points="19,14 27,22 19,30" fill="none" stroke="#fff" stroke-width="1.5"/></svg></div>
</section>

<h2 class="section-title" style="top:636px">Featured Products</h2>

<article class="product-card" style="left:142px;top:733px">
  <div class="product-img"><span role="img" aria-label="Protein powder tub" style="background:linear-gradient(180deg,#222 20%,#2ec3e6 20%,#1aa8cc)"></span></div>
  <div class="rating"><b>★★★★★</b> (1)</div><div class="product-name">Product 1</div><a class="btn-outline" href="#">Details</a>
</article>
<article class="product-card" style="left:455px;top:733px">
  <div class="product-img"><span role="img" aria-label="Grey blazer over white shirt and jeans" style="background:linear-gradient(90deg,#333,#9a9a9a 40%,#f2f2f2 50%,#9a9a9a 60%,#333)"></span></div>
  <div class="rating"><b>★★★★★</b> (77)</div><div class="product-name">Product 2</div><a class="btn-outline" href="#">Details</a>
</article>
<article class="product-card" style="left:768px;top:733px">
  <div class="product-img"><span role="img" aria-label="Pink floral sundress" style="width:90px;background:linear-gradient(180deg,#e7b7c2,#b8c7a6 60%,#d98aa0)"></span></div>
  <div class="badge"></div>
  <div class="rating"><b>★★★★★</b> (255)</div><div class="product-name">Product 3</div><a class="btn-outline" href="#">Details</a>
</article>
<article class="product-card" style="left:142px;top:1202px">
  <div class="product-img"><span role="img" aria-label="Dark green zip jacket" style="width:170px;height:210px;background:#1f5750"></span></div>
  <div class="badge"></div>
  <div class="rating"><b>★★★★★</b> (1)</div><div class="product-name">Product 4</div><a class="btn-outline" href="#">Details</a>
</article>
<article class="product-card" style="left:455px;top:1202px">
  <div class="product-img"><span role="img" aria-label="Red halter swing dress" style="width:190px;background:linear-gradient(180deg,#d4202a,#c81d25)"></span></div>
  <div class="rating"><b>★★★★★</b> (77)</div><div class="product-name">Product 5</div><a class="btn-outline" href="#">Details</a>
</article>
<article class="product-card" style="left:768px;top:1202px">
  <div class="product-img"><span role="img" aria-label="Nutrition shake tub and sachet" style="width:150px;height:180px;background:linear-gradient(180deg,#e9ede6,#8cc63f 40%,#e9ede6)"></span></div>
  <div class="rating"><b>★★★★★</b> (255)</div><div class="product-name">Product 6</div><a class="btn-outline" href="#">Details</a>
</article>

<a class="btn-solid" href="#" style="left:537px;top:1663px;width:126px;height:35px;line-height:35px">View All</a>

<section class="promo">
  <div class="promo-photo" role="img" aria-label="Man in sunglasses and striped waistcoat"></div>
  <h2>DENIM JACKET FOR MEN</h2>
  <div class="sub">SAVE UP TO 70% OFF MEN'S &amp; BOYS CLOTHINGS</div>
  <p>Donec dolor sem, rhoncus at purus sit amet, dapibus convallis justo. Duis sit amet ex quis velit sollicitudin accumsan.</p>
  <a class="btn-solid" href="#" style="left:589px;top:243px;width:134px;height:35px;line-height:35px">View Details</a>
</section>

<h2 class="section-title" style="top:2224px">About Vantor</h2>
<div class="about-copy">
  <p>Lorem ipsum dolor sit amet, consectetuer adipiscing elit, sed diamlet me nonummy nibh euismod tincidunt ut laoreet dolore.</p>
  <p>Magna aliquam erat volutpat ut wisi enim ad minim veniam, quis nostrud exerci tation ullamcorper suscipit lobortis nisl ut aliquip ex ea commodo consequat.</p>
  <p>Duis autem vel eum iriure dolor in hendrerit in vulputate velit esse molestie consequat, vel illum dolore eu feugiat nulla facilisis at vero eros ettlemn accumsan et iusto odio dignissim qui blandit praesent luptatum zzril delenit augue duis dolore te feugait nulla facilisi.</p>
</div>
<a class="btn-solid" href="#" style="left:142px;top:2581px;width:126px;height:35px;line-height:35px">Know More</a>
<div class="about-frame"></div>
<div class="about-photo" role="img" aria-label="Smiling couple in sun hats outdoors"></div>

<section class="blogs">
  <h2 class="section-title" style="top:65px">Latest Blogs</h2>
  <div class="round-arrow" style="left:71px"><svg width="12" height="12"><polyline points="8,1 3,6 8,11" fill="none" stroke="#333" stroke-width="1.8"/></svg></div>
  <article class="blog-card" style="left:142px">
    <div class="blog-img" role="img" aria-label="Couple jogging in a park" style="background:linear-gradient(180deg,#8ab35a,#4f7d2e)"></div>
    <h3>Maecenas quis justo et sapien conseq volutpat quis id diam</h3>
    <p>Nullam tincidunt lobortis felis, in accumsan lacus varius in. Donec ut diam eget augue viverra euismod...</p>
  </article>
  <article class="blog-card" style="left:455px">
    <div class="blog-img" role="img" aria-label="Woman doing floor exercises on a mat" style="background:linear-gradient(180deg,#b9a797,#5a4d45)"></div>
    <h3>Maecenas quis justo et sapien conseq volutpat quis id diam</h3>
    <p>Nullam tincidunt lobortis felis, in accumsan lacus varius in. Donec ut diam eget augue viverra euismod...</p>
  </article>
  <article class="blog-card" style="left:768px">
    <div class="blog-img" role="img" aria-label="Traveller reading a map beside a vintage plane" style="background:linear-gradient(180deg,#8d8a80,#4a463d)"></div>
    <h3>Maecenas quis justo et sapien conseq volutpat quis id diam</h3>
    <p>Nullam tincidunt lobortis felis, in accumsan lacus varius in. Donec ut diam eget augue viverra euismod...</p>
  </article>
  <div class="round-arrow" style="left:1095px"><svg width="12" height="12"><polyline points="4,1 9,6 4,11" fill="none" stroke="#333" stroke-width="1.8"/></svg></div>
  <a class="btn-solid" href="#" style="left:537px;top:537px;width:126px;height:35px;line-height:35px">View All</a>
</section>

<section class="newsletter">
  <h2>SUBSCRIBE TO NEWSLETTER</h2>
  <div class="lede">Sign up to get the latest on sales, new releases and more...</div>
  <div class="email-field">Your Email<a class="btn-solid" href="#">SUBSCRIBE</a></div>
</section>

<footer class="site-footer">
  <div class="foot-head" style="left:142px">QUICK LINKS</div>
  <ul class="quick-links"><li>Home</li><li>About Us</li><li>Products</li><li>Blog</li><li>Contact Us</li></ul>

  <div class="foot-head" style="left:330px">CONTACT DETAILS</div>
  <div class="contact-row" style="top:112px">
    <span class="icon-ring"><svg width="12" height="14" viewBox="0 0 12 14"><path d="M6 13C2 8 1 6.5 1 5a5 5 0 0 1 10 0c0 1.5-1 3-5 8z" fill="none" stroke="#f0a22a" stroke-width="1.4"/><circle cx="6" cy="5" r="1.6" fill="#f0a22a"/></svg></span>
    <div><b>VANTOR</b><br>48, Harlow Ridge, Lorem ipsum,<br>KS 60417</div>
  </div>
  <div class="contact-row" style="top:186px">
    <span class="icon-ring"><svg width="13" height="10" viewBox="0 0 13 10"><rect x="0.7" y="0.7" width="11.6" height="8.6" fill="none" stroke="#f0a22a" stroke-width="1.3"/><polyline points="1,1 6.5,5.5 12,1" fill="none" stroke="#f0a22a" stroke-width="1.3"/></svg></span>
    <div style="padding-top:4px">info@vantorwear.com</div>
  </div>
  <div class="contact-row" style="top:234px">
    <span class="icon-ring"><svg width="12" height="12" viewBox="0 0 12 12"><path d="M2 1l2.5 0 1 2.8-1.5 1a7 7 0 0 0 3.2 3.2l1-1.5 2.8 1V10a1.2 1.2 0 0 1-1.2 1.2A9.5 9.5 0 0 1 .8 2.2 1.2 1.2 0 0 1 2 1z" fill="#f0a22a"/></svg></span>
    <div style="padding-top:4px">(00) 014 220 7391</div>
  </div>

  <div class="foot-head" style="left:651px">FOLLOW US ON</div>
  <div class="social-row" style="top:116px"><i></i>Community</div>
  <div class="social-row" style="top:154px"><i></i>Updates</div>
  <div class="social-row" style="top:193px"><i></i>Videos</div>
  <div class="social-row" style="top:232px"><i></i>Gallery</div>

  <div class="foot-brand"><i></i>VANTOR</div>
  <div class="foot-rule"></div>
  <div class="copyright">Copyright © 2019 VANTOR WEAR AND FUEL. All Rights Reserved</div>
</footer>

</body>
</html>
```